I would like to modify/update my 2 step login screen

I want a more modern looking login page for our document imaging application. I need to keep all of the same elements and buttons that currently exist. The first 2 screens are the login. The 3rd is a screenshot of the actual application home page.

```html
<!DOCTYPE html>
<html lang="en">
<head>
<meta charset="utf-8">
<title>Quorvale Docsys – Login States</title>
<link href="https://fonts.googleapis.com/css2?family=Inter:wght@400;500;600;700&display=swap" rel="stylesheet">
<style>
:root{
  --canvas:#efefef;
  --header:#3a3b3d;
  --page:#fafafa;
  --card:#ffffff;
  --ink:#222326;
  --muted:#8a8c90;
  --line:#e3e4e6;
  --band:#f1f1f2;
  --green:#4caf50;
  --disabled:#c9cacc;
  --blue:#4a7fd6;
  --red:#e5484d;
  --brand-red:#b3261e;
  --lock:#3d7fb8;
  --link:#2d6cc0;
  --icon-bg:#f2f2f3;
}
*{box-sizing:border-box;margin:0;padding:0}
html,body{width:1200px;height:482px;overflow:hidden;background:var(--canvas);font-family:"Inter",sans-serif;color:var(--ink)}
.stage{position:relative;width:2576px;height:1036px;transform:scale(.46584);transform-origin:0 0}
.screen{position:absolute;width:797px;height:448px;background:var(--page);overflow:hidden}
.screen.c1{left:46px}.screen.c2{left:889px}.screen.c3{left:1732px}
.screen.r1{top:46px}.screen.r2{top:541px}
.topbar{position:absolute;left:0;top:0;width:100%;height:131px;background:var(--header)}
.wordmark{position:absolute;left:0;right:0;top:30px;text-align:center;color:#fff;font-weight:700;font-size:14px;letter-spacing:.5px;line-height:1.1}
.wordmark span{display:block}
.card{position:absolute;left:212px;top:89px;width:373px;background:var(--card);border-radius:4px;box-shadow:0 1px 4px rgba(0,0,0,.12);overflow:hidden}
.tabs{display:flex;height:42px;border-bottom:1px solid var(--line)}
.tab{flex:1;display:flex;align-items:center;justify-content:center;border-bottom:2px solid transparent}
.tab.active{border-bottom-color:var(--green)}
.tab-mark{font-weight:700;font-size:10px;color:var(--brand-red)}
.body{padding:24px 37px 14px}
.title-row{display:flex;justify-content:space-between;align-items:center;margin-bottom:14px}
.title{font-size:14px;font-weight:600}
.error-msg{font-size:6.5px;color:var(--red)}
.field{display:flex;align-items:center;height:31px;border:1px solid var(--line);border-radius:16px;padding:0 10px 0 4px;margin-bottom:7px;background:#fff}
.field.focus{border-color:var(--blue);box-shadow:0 0 0 1px rgba(74,127,214,.25)}
.field.error{border-color:var(--red)}
.field-icon{width:23px;height:23px;border-radius:50%;background:var(--icon-bg);display:flex;align-items:center;justify-content:center;flex:none}
.field-text{flex:1;margin-left:10px;line-height:1.25}
.placeholder{font-size:7.5px;color:var(--muted)}
.label{display:block;font-size:5.5px;color:var(--muted)}
.value{display:block;font-size:7.5px;color:var(--ink)}
.dots{letter-spacing:1px;font-size:9px;line-height:1}
.caret{display:inline-block;width:1px;height:8px;background:var(--ink);vertical-align:middle;margin-left:1px}
.field-tool{margin-left:8px;display:flex}
.actions{display:flex;align-items:center;margin-top:16px}
.check{width:10px;height:10px;border:1px solid #b5b6b9;border-radius:2px;display:flex;align-items:center;justify-content:center}
.check.on{background:var(--green);border-color:var(--green)}
.remember{font-size:7px;margin-left:7px}
.divider{width:1px;height:10px;background:var(--line);margin:0 7px}
.forgot{font-size:7px;color:var(--link)}
.btn{margin-left:auto;width:58px;height:22px;border-radius:11px;border:none;color:#fff;font-size:6.5px;font-weight:600;display:flex;align-items:center;justify-content:center;font-family:inherit}
.btn.off{background:var(--disabled)}
.btn.on{background:var(--green)}
.notice{background:var(--band);font-size:6px;text-align:center;padding:5px 0;color:#444}
.notice b{font-weight:600}
.providers{display:flex;border-top:1px solid var(--line);height:49px}
.provider{flex:1;display:flex;flex-direction:column;align-items:center;justify-content:center;gap:6px;font-size:7px;color:#444}
.provider+.provider{border-left:1px solid var(--line)}
.provider-dot{width:11px;height:11px;border-radius:50%;background:#9a9ca0}
.footer{position:absolute;left:0;right:0;top:396px;text-align:center;font-size:6px}
.footer-links{color:#333}
.footer-links i{font-style:normal;color:var(--muted);margin:0 5px}
.copyright{color:var(--muted);margin-top:8px}
</style>
</head>
<body>
<div class="stage">

<!-- Row 1: QVDS login states -->
<section class="screen r1 c1">
  <div class="topbar"><div class="wordmark"><span>QUORVALE</span><span>DOCSYS</span></div></div>
  <div class="card">
    <div class="tabs">
      <div class="tab active"><span class="tab-mark">QVDS</span></div>
      <div class="tab"><svg width="10" height="12" viewBox="0 0 10 12"><rect x="1" y="5" width="8" height="7" rx="1" fill="var(--lock)"/><path d="M3 5V3.5a2 2 0 0 1 4 0V5" fill="none" stroke="var(--lock)" stroke-width="1.4"/></svg></div>
    </div>
    <div class="body">
      <div class="title-row"><h1 class="title">QVDS Login</h1></div>
      <div class="field">
        <span class="field-icon"><svg width="11" height="10" viewBox="0 0 11 10"><rect x="1" y="1" width="9" height="3.5" rx="1" fill="none" stroke="#555" stroke-width="1"/><rect x="1" y="5.5" width="9" height="3.5" rx="1" fill="none" stroke="#555" stroke-width="1"/></svg></span>
        <span class="field-text"><span class="placeholder">Database</span></span>
      </div>
      <div class="actions"><span class="check"></span><span class="remember">Remember Me</span><button class="btn off">LOGIN</button></div>
    </div>
    <div class="notice">All activity on this site is being recorded. Your IP Address is being saved as '<b>192.168.168.134</b>'.</div>
    <div class="providers">
      <div class="provider"><span class="provider-dot"></span>Login with Plenvoy</div>
      <div class="provider"><span class="provider-dot"></span>Login with Brelvik</div>
      <div class="provider"><span class="provider-dot"></span>Login with Oskavo</div>
    </div>
  </div>
  <div class="footer"><div class="footer-links">Privacy<i>•</i>Remote Support<i>•</i>Contact Us</div><div class="copyright">Copyright 2007-2024 Quorvale Docsys</div></div>
</section>

<section class="screen r1 c2">
  <div class="topbar"><div class="wordmark"><span>QUORVALE</span><span>DOCSYS</span></div></div>
  <div class="card">
    <div class="tabs">
      <div class="tab active"><span class="tab-mark">QVDS</span></div>
      <div class="tab"><svg width="10" height="12" viewBox="0 0 10 12"><rect x="1" y="5" width="8" height="7" rx="1" fill="var(--lock)"/><path d="M3 5V3.5a2 2 0 0 1 4 0V5" fill="none" stroke="var(--lock)" stroke-width="1.4"/></svg></div>
    </div>
    <div class="body">
      <div class="title-row"><h1 class="title">QVDS Login</h1></div>
      <div class="field focus">
        <span class="field-icon"><svg width="11" height="10" viewBox="0 0 11 10"><rect x="1" y="1" width="9" height="3.5" rx="1" fill="none" stroke="#555" stroke-width="1"/><rect x="1" y="5.5" width="9" height="3.5" rx="1" fill="none" stroke="#555" stroke-width="1"/></svg></span>
        <span class="field-text"><span class="label">Database</span><span class="value">ABC12345<span class="caret"></span></span></span>
        <span class="field-tool"><svg width="8" height="8" viewBox="0 0 8 8"><path d="M1 1l6 6M7 1L1 7" stroke="#777" stroke-width="1"/></svg></span>
      </div>
      <div class="actions"><span class="check"></span><span class="remember">Remember Me</span><button class="btn on">LOGIN</button></div>
    </div>
    <div class="notice">All activity on this site is being recorded. Your IP Address is being saved as '<b>192.168.168.134</b>'.</div>
    <div class="providers">
      <div class="provider"><span class="provider-dot"></span>Login with Plenvoy</div>
      <div class="provider"><span class="provider-dot"></span>Login with Brelvik</div>
      <div class="provider"><span class="provider-dot"></span>Login with Oskavo</div>
    </div>
  </div>
  <div class="footer"><div class="footer-links">Privacy<i>•</i>Remote Support<i>•</i>Contact Us</div><div class="copyright">Copyright 2007-2024 Quorvale Docsys</div></div>
</section>

<section class="screen r1 c3">
  <div class="topbar"><div class="wordmark"><span>QUORVALE</span><span>DOCSYS</span></div></div>
  <div class="card">
    <div class="tabs">
      <div class="tab active"><span class="tab-mark">QVDS</span></div>
      <div class="tab"><svg width="10" height="12" viewBox="0 0 10 12"><rect x="1" y="5" width="8" height="7" rx="1" fill="var(--lock)"/><path d="M3 5V3.5a2 2 0 0 1 4 0V5" fill="none" stroke="var(--lock)" stroke-width="1.4"/></svg></div>
    </div>
    <div class="body">
      <div class="title-row"><h1 class="title">QVDS Login</h1><span class="error-msg">Login failed! Please enter correct entries.</span></div>
      <div class="field error">
        <span class="field-icon"><svg width="11" height="10" viewBox="0 0 11 10"><rect x="1" y="1" width="9" height="3.5" rx="1" fill="none" stroke="#555" stroke-width="1"/><rect x="1" y="5.5" width="9" height="3.5" rx="1" fill="none" stroke="#555" stroke-width="1"/></svg></span>
        <span class="field-text"><span class="label">Database</span><span class="value">ABC12345XYZ</span></span>
        <span class="field-tool"><svg width="8" height="8" viewBox="0 0 8 8"><path d="M1 1l6 6M7 1L1 7" stroke="#777" stroke-width="1"/></svg></span>
      </div>
      <div class="actions"><span class="check on"><svg width="7" height="6" viewBox="0 0 7 6"><path d="M1 3l2 2 3-4" fill="none" stroke="#fff" stroke-width="1.2"/></svg></span><span class="remember">Remember Me</span><button class="btn on">LOGIN</button></div>
    </div>
    <div class="notice">All activity on this site is being recorded. Your IP Address is being saved as '<b>192.168.168.134</b>'.</div>
    <div class="providers">
      <div class="provider"><span class="provider-dot"></span>Login with Plenvoy</div>
      <div class="provider"><span class="provider-dot"></span>Login with Brelvik</div>
      <div class="provider"><span class="provider-dot"></span>Login with Oskavo</div>
    </div>
  </div>
  <div class="footer"><div class="footer-links">Privacy<i>•</i>Remote Support<i>•</i>Contact Us</div><div class="copyright">Copyright 2007-2024 Quorvale Docsys</div></div>
</section>

<!-- Row 2: Classic login states -->
<section class="screen r2 c1">
  <div class="topbar"><div class="wordmark"><span>QUORVALE</span><span>DOCSYS</span></div></div>
  <div class="card">
    <div class="tabs">
      <div class="tab"><span class="tab-mark">QVDS</span></div>
      <div class="tab active"><svg width="10" height="12" viewBox="0 0 10 12"><rect x="1" y="5" width="8" height="7" rx="1" fill="var(--lock)"/><path d="M3 5V3.5a2 2 0 0 1 4 0V5" fill="none" stroke="var(--lock)" stroke-width="1.4"/></svg></div>
    </div>
    <div class="body">
      <div class="title-row"><h1 class="title">Classic Login</h1></div>
      <div class="field">
        <span class="field-icon"><svg width="10" height="11" viewBox="0 0 10 11"><circle cx="5" cy="3.2" r="2.2" fill="none" stroke="#555"/><path d="M1 10.5a4 4 0 0 1 8 0" fill="none" stroke="#555"/></svg></span>
        <span class="field-text"><span class="placeholder">Username</span></span>
      </div>
      <div class="field">
        <span class="field-icon"><svg width="11" height="11" viewBox="0 0 11 11"><circle cx="7" cy="4" r="2.6" fill="none" stroke="#555"/><path d="M5.2 5.8L1 10M2.5 8.5l1.2 1.2" fill="none" stroke="#555"/></svg></span>
        <span class="field-text"><span class="placeholder">Password</span></span>
        <span class="field-tool"><svg width="10" height="8" viewBox="0 0 10 8"><path d="M1 4s1.6-3 4-3 4 3 4 3-1.6 3-4 3-4-3-4-3z" fill="none" stroke="#777" stroke-width=".9"/><path d="M2 7.5L8 .5" stroke="#777" stroke-width=".9"/></svg></span>
      </div>
      <div class="actions"><span class="check"></span><span class="remember">Remember Me</span><span class="divider"></span><span class="forgot">Forgot Password?</span><button class="btn off">LOGIN</button></div>
    </div>
    <div class="providers">
      <div class="provider"><span class="provider-dot"></span>Login with Plenvoy</div>
      <div class="provider"><span class="provider-dot"></span>Login with Brelvik</div>
      <div class="provider"><span class="provider-dot"></span>Login with Oskavo</div>
    </div>
  </div>
  <div class="footer"><div class="footer-links">Privacy<i>•</i>Remote Support<i>•</i>Contact Us</div><div class="copyright">Copyright 2007-2024 Quorvale Docsys</div></div>
</section>

<section class="screen r2 c2">
  <div class="topbar"><div class="wordmark"><span>QUORVALE</span><span>DOCSYS</span></div></div>
  <div class="card">
    <div class="tabs">
      <div class="tab"><span class="tab-mark">QVDS</span></div>
      <div class="tab active"><svg width="10" height="12" viewBox="0 0 10 12"><rect x="1" y="5" width="8" height="7" rx="1" fill="var(--lock)"/><path d="M3 5V3.5a2 2 0 0 1 4 0V5" fill="none" stroke="var(--lock)" stroke-width="1.4"/></svg></div>
    </div>
    <div class="body">
      <div class="title-row"><h1 class="title">Classic Login</h1></div>
      <div class="field">
        <span class="field-icon"><svg width="10" height="11" viewBox="0 0 10 11"><circle cx="5" cy="3.2" r="2.2" fill="none" stroke="#555"/><path d="M1 10.5a4 4 0 0 1 8 0" fill="none" stroke="#555"/></svg></span>
        <span class="field-text"><span class="label">Username</span><span class="value">JohnDoe123</span></span>
        <span class="field-tool"><svg width="8" height="8" viewBox="0 0 8 8"><path d="M1 1l6 6M7 1L1 7" stroke="#777" stroke-width="1"/></svg></span>
      </div>
      <div class="field focus">
        <span class="field-icon"><svg width="11" height="11" viewBox="0 0 11 11"><circle cx="7" cy="4" r="2.6" fill="none" stroke="#555"/><path d="M5.2 5.8L1 10M2.5 8.5l1.2 1.2" fill="none" stroke="#555"/></svg></span>
        <span class="field-text"><span class="label">Password</span><span class="value dots">●●●<span class="caret"></span></span></span>
        <span class="field-tool"><svg width="10" height="8" viewBox="0 0 10 8"><path d="M1 4s1.6-3 4-3 4 3 4 3-1.6 3-4 3-4-3-4-3z" fill="none" stroke="#777" stroke-width=".9"/><path d="M2 7.5L8 .5" stroke="#777" stroke-width=".9"/></svg></span>
        <span class="field-tool"><svg width="8" height="8" viewBox="0 0 8 8"><path d="M1 1l6 6M7 1L1 7" stroke="#777" stroke-width="1"/></svg></span>
      </div>
      <div class="actions"><span class="check"></span><span class="remember">Remember Me</span><span class="divider"></span><span class="forgot">Forgot Password?</span><button class="btn on">LOGIN</button></div>
    </div>
    <div class="providers">
      <div class="provider"><span class="provider-dot"></span>Login with Plenvoy</div>
      <div class="provider"><span class="provider-dot"></span>Login with Brelvik</div>
      <div class="provider"><span class="provider-dot"></span>Login with Oskavo</div>
    </div>
  </div>
  <div class="footer"><div class="footer-links">Privacy<i>•</i>Remote Support<i>•</i>Contact Us</div><div class="copyright">Copyright 2007-2024 Quorvale Docsys</div></div>
</section>

<section class="screen r2 c3">
  <div class="topbar"><div class="wordmark"><span>QUORVALE</span><span>DOCSYS</span></div></div>
  <div class="card">
    <div class="tabs">
      <div class="tab"><span class="tab-mark">QVDS</span></div>
      <div class="tab active"><svg width="10" height="12" viewBox="0 0 10 12"><rect x="1" y="5" width="8" height="7" rx="1" fill="var(--lock)"/><path d="M3 5V3.5a2 2 0 0 1 4 0V5" fill="none" stroke="var(--lock)" stroke-width="1.4"/></svg></div>
    </div>
    <div class="body">
      <div class="title-row"><h1 class="title">Classic Login</h1><span class="error-msg">Login failed! Please enter correct entries.</span></div>
      <div class="field error">
        <span class="field-icon"><svg width="10" height="11" viewBox="0 0 10 11"><circle cx="5" cy="3.2" r="2.2" fill="none" stroke="#555"/><path d="M1 10.5a4 4 0 0 1 8 0" fill="none" stroke="#555"/></svg></span>
        <span class="field-text"><span class="label">Username</span><span class="value">john.doe</span></span>
        <span class="field-tool"><svg width="8" height="8" viewBox="0 0 8 8"><path d="M1 1l6 6M7 1L1 7" stroke="#777" stroke-width="1"/></svg></span>
      </div>
      <div class="field error">
        <span class="field-icon"><svg width="11" height="11" viewBox="0 0 11 11"><circle cx="7" cy="4" r="2.6" fill="none" stroke="#555"/><path d="M5.2 5.8L1 10M2.5 8.5l1.2 1.2" fill="none" stroke="#555"/></svg></span>
        <span class="field-text"><span class="label">Password</span><span class="value dots">●●●●●●</span></span>
        <span class="field-tool"><svg width="10" height="8" viewBox="0 0 10 8"><path d="M1 4s1.6-3 4-3 4 3 4 3-1.6 3-4 3-4-3-4-3z" fill="none" stroke="#777" stroke-width=".9"/><path d="M2 7.5L8 .5" stroke="#777" stroke-width=".9"/></svg></span>
        <span class="field-tool"><svg width="8" height="8" viewBox="0 0 8 8"><path d="M1 1l6 6M7 1L1 7" stroke="#777" stroke-width="1"/></svg></span>
      </div>
      <div class="actions"><span class="check on"><svg width="7" height="6" viewBox="0 0 7 6"><path d="M1 3l2 2 3-4" fill="none" stroke="#fff" stroke-width="1.2"/></svg></span><span class="remember">Remember Me</span><span class="divider"></span><span class="forgot">Forgot Password?</span><button class="btn on">LOGIN</button></div>
    </div>
    <div class="providers">
      <div class="provider"><span class="provider-dot"></span>Login with Plenvoy</div>
      <div class="provider"><span class="provider-dot"></span>Login with Brelvik</div>
      <div class="provider"><span class="provider-dot"></span>Login with Oskavo</div>
    </div>
  </div>
  <div class="footer"><div class="footer-links">Privacy<i>•</i>Remote Support<i>•</i>Contact Us</div><div class="copyright">Copyright 2007-2024 Quorvale Docsys</div></div>
</section>

</div>
</body>
</html>
```